Kestal-Materials. Limestone; improving the world

New Limestone company and need logo design.
Limestone offsets carbon mitigation industries restore and replenish soil fertilities in the Prairies, the breadbasket of the world. At the same time, Limestone is proving a critical emergent component of carbon capture sequestration technology will therefore play a critical role in the development of the western Canadian energy industries
Our limestone resources are situated in the foothills of the Canadian Rockies well-positioned above the sprawling fields of the vast peace district.
Agriculture and oli sites
Kestal Materials
3 page

```html
<!DOCTYPE html>
<html lang="en">
<head>
<meta charset="utf-8">
<title>Kestal Materials</title>
<link href="https://fonts.googleapis.com/css2?family=Montserrat:wght@500;600;700;800&family=Poppins:wght@600&family=Hind:wght@400;500&display=swap" rel="stylesheet">
<style>
:root{
  --green:#45b31b;
  --ink:#1f1f1f;
  --text:#3a3a3a;
  --white:#ffffff;
  --mist:#f4f0f0;
  --footer:#1d1d1d;
  --footer-line:#3a3a3a;
}
*{box-sizing:border-box;margin:0;padding:0}
html,body{width:1200px;height:3289px;overflow:hidden}
body{font-family:"Hind",sans-serif;color:var(--text);background:var(--white)}
.wrap{width:940px;margin:0 auto;position:relative}
.btn{display:inline-block;background:var(--green);color:var(--white);font-family:"Montserrat",sans-serif;font-weight:700;text-transform:uppercase;text-decoration:none;text-align:center}
.rule{display:block;width:62px;height:2px;background:var(--ink);margin:0 auto}
.section-title{font-family:"Montserrat",sans-serif;font-weight:800;font-size:24px;color:var(--ink);text-align:center;text-transform:uppercase}
.backdrop{position:absolute;inset:0}

/* header */
.site-header{height:73px}
.site-header .wrap{display:flex;justify-content:space-between;align-items:center;height:73px}
.brand{font-family:"Poppins",sans-serif;font-weight:600;font-size:24px;color:#2a2a2a}
.nav{display:flex;gap:29px;font-family:"Montserrat",sans-serif;font-weight:600;font-size:13px;color:#2a2a2a;margin-top:4px}
.nav a{color:inherit;text-decoration:none}
.nav .active{color:var(--green);text-decoration:underline;text-underline-offset:4px}

/* hero */
.hero{height:550px;position:relative;overflow:hidden}
.hero .backdrop{background:linear-gradient(180deg,#4f4d40 0%,#676451 40%,#8f7a2c 68%,#5b5a20 86%,#3d3e16 100%)}
.hero .wrap{padding-top:80px}
.hero h1{font-family:"Montserrat",sans-serif;font-weight:800;font-size:38px;color:var(--white);letter-spacing:.5px}
.hero p{font-size:20px;line-height:24px;color:var(--white);margin-top:16px;width:345px}
.hero .btn{font-size:14px;width:133px;height:46px;line-height:46px;margin-top:27px}
.dots{position:absolute;left:0;right:0;top:504px;display:flex;justify-content:center;gap:11px;align-items:center}
.dots span{width:7px;height:7px;border-radius:50%;background:var(--white)}
.dots .on{width:11px;height:11px;background:none;border:2px solid var(--green)}

/* welcome */
.welcome{height:432px}
.welcome .wrap{display:flex;padding-top:46px;gap:40px}
.welcome-photo{width:460px;height:337px;background:linear-gradient(135deg,#d8d2c8,#b9b2a6 50%,#a39b8e)}
.welcome-copy{width:440px;padding-top:4px}
.welcome-copy .kicker{font-family:"Montserrat",sans-serif;font-weight:600;font-size:18px;color:var(--ink)}
.welcome-copy h2{font-family:"Montserrat",sans-serif;font-weight:800;font-size:24px;color:var(--ink);margin-top:2px}
.welcome-copy .rule{margin:10px 0 0;width:94px}
.welcome-copy p{font-size:17px;line-height:24.8px;margin-top:33px}
.welcome-copy .btn{font-size:14px;width:118px;height:35px;line-height:35px;margin-top:37px}

/* products */
.products{height:505px;background:var(--mist);padding-top:36px}
.products .rule{margin-top:14px}
.product-grid{display:flex;gap:13px;margin-top:37px}
.product-card{width:225px;height:278px;background:var(--white);padding:0 32px;position:relative}
.product-card h3{font-family:"Montserrat",sans-serif;font-weight:600;font-size:16px;line-height:19px;color:var(--ink);height:88px;display:flex;align-items:flex-end;padding-bottom:8px}
.product-card p{font-size:13px;line-height:17.5px;margin-top:15px}
.product-card .btn{position:absolute;left:34px;top:229px;font-size:10px;width:84px;height:24px;line-height:24px}
.view-all{display:block;margin:38px auto 0;width:156px;height:30px;line-height:26px;border:2px solid var(--green);color:var(--green);font-family:"Montserrat",sans-serif;font-weight:700;font-size:12px;text-align:center;text-transform:uppercase}

/* sustainability */
.sustain{height:446px;position:relative;overflow:hidden}
.sustain .backdrop{background:linear-gradient(180deg,#1d6fb0 0%,#4f9bd2 35%,#c4dbe8 62%,#6fae2f 80%,#3e7f17 100%)}
.sustain .wrap{padding-top:52px}
.sustain h2{font-family:"Montserrat",sans-serif;font-weight:800;font-size:31px;color:var(--white)}
.sustain p{font-size:17px;line-height:24.8px;color:var(--white);width:412px;margin-top:12px}
.sustain .btn{font-size:14px;width:118px;height:34px;line-height:34px;margin-top:33px;margin-left:2px}

/* blog */
.blog{height:587px;padding-top:43px}
.blog .rule{margin-top:16px}
.blog-grid{display:flex;gap:26px;margin-top:38px;padding-left:2px}
.blog-card{width:295px;height:407px;background:var(--white);box-shadow:0 1px 6px rgba(0,0,0,.12);position:relative}
.blog-photo{height:192px}
.photo-rock{background:linear-gradient(180deg,#c7a66b 0,#8f8a76 40%,#6c6a5f 70%,#4d5a2d 100%)}
.photo-valley{background:linear-gradient(180deg,#6d8aa0 0,#4f6f62 30%,#3e7a2a 65%,#2f6a1e 100%)}
.photo-bulb{background:linear-gradient(180deg,#0a1c2a 0,#0d2b3a 50%,#061522 100%)}
.blog-card h3{font-family:"Montserrat",sans-serif;font-weight:600;font-size:15px;line-height:20px;color:var(--ink);padding:24px 27px 0}
.blog-card p{font-size:14px;line-height:20px;padding:12px 70px 0 28px}
.blog-card .btn{position:absolute;left:31px;top:346px;font-size:10px;width:91px;height:28px;line-height:28px}

/* call to action */
.cta{height:357px;position:relative;text-align:center;padding-top:100px}
.cta .backdrop{background:linear-gradient(180deg,#5b5646 0%,#6e6850 35%,#7c7a6c 60%,#5c5a50 100%)}
.cta-body{position:relative}
.cta h2{font-family:"Montserrat",sans-serif;font-weight:800;font-size:24px;color:var(--white)}
.cta p{font-size:19.5px;line-height:23px;color:var(--white);width:720px;margin:14px auto 0}
.cta .btn{font-size:14px;width:126px;height:35px;line-height:35px;margin-top:20px}

/* footer */
.site-footer{height:339px;background:var(--footer);color:var(--white)}
.footer-top{height:265px;position:relative}
.footer-brand{position:absolute;left:35px;top:114px;font-family:"Poppins",sans-serif;font-weight:600;font-size:25px}
.footer-col{position:absolute;top:49px}
.footer-col h4{font-family:"Montserrat",sans-serif;font-weight:700;font-size:12.5px;letter-spacing:.3px}
.col-menu{left:368px}
.col-menu ul{list-style:none;margin-top:22px}
.col-menu li{font-family:"Montserrat",sans-serif;font-size:11.5px;line-height:20px}
.col-contact{left:559px}
.col-follow{left:826px}
.info{display:flex;align-items:center;gap:10px;margin-top:17px;font-family:"Montserrat",sans-serif;font-size:11.5px;line-height:15.5px}
.footer-col h4 + .info{margin-top:21px}
.info .ico{width:24px;height:24px;border-radius:50%;background:var(--white);flex:none;display:flex;align-items:center;justify-content:center}
.footer-line{width:940px;margin:0 auto;height:1px;background:var(--footer-line)}
.copyright{text-align:center;font-family:"Montserrat",sans-serif;font-size:9px;padding-top:34px}
</style>
</head>
<body>

<header class="site-header">
  <div class="wrap">
    <div class="brand">Kestal Materials</div>
    <nav class="nav">
      <a class="active">HOME</a><a>ABOUT US</a><a>PRODUCTS</a><a>SUSTAINABILITY</a><a>CAREERS</a><a>CONTACT US</a>
    </nav>
  </div>
</header>

<section class="hero">
  <div class="backdrop" role="img" aria-label="Glass globe resting on sunlit moss"></div>
  <div class="wrap">
    <h1>LIMESTONE</h1>
    <p>There are many variations of passages of Lorem Ipsum available.</p>
    <a class="btn">Read More</a>
  </div>
  <div class="dots"><span></span><span></span><span class="on"></span><span></span><span></span></div>
</section>

<section class="welcome">
  <div class="wrap">
    <div class="welcome-photo" role="img" aria-label="Pile of crushed white limestone rocks"></div>
    <div class="welcome-copy">
      <div class="kicker">WELCOME TO</div>
      <h2>KESTAL MATERIALS</h2>
      <span class="rule"></span>
      <p>Lorem Ipsum is simply dummy text of the printing and typesetting industry. Lorem Ipsum has been the industry's standard dummy text ever since the 1500s, when an unknown printer took a galley of type and scrambled it to make a type specimen book. It has survived not only five centuries, but also the leap into electronic typesetting, remaining essentially unchanged.</p>
      <a class="btn">Read More</a>
    </div>
  </div>
</section>

<section class="products">
  <div class="wrap">
    <h2 class="section-title">Our Products</h2>
    <span class="rule"></span>
    <div class="product-grid">
      <article class="product-card"><h3>High-calcium<br>Quicklime</h3><p>Lorem Ipsum is simply dummy text of the printing and typesetting industry. Lorem Ipsum has been the industry's standard</p><a class="btn">Read More</a></article>
      <article class="product-card"><h3>Pulverized<br>Limestone<br>Products</h3><p>Lorem Ipsum is simply dummy text of the printing and typesetting industry. Lorem Ipsum has been the industry's standard</p><a class="btn">Read More</a></article>
      <article class="product-card"><h3>Chemical<br>Limestone</h3><p>Lorem Ipsum is simply dummy text of the printing and typesetting industry. Lorem Ipsum has been the industry's standard</p><a class="btn">Read More</a></article>
      <article class="product-card"><h3>Construction<br>Stone</h3><p>Lorem Ipsum is simply dummy text of the printing and typesetting industry. Lorem Ipsum has been the industry's standard</p><a class="btn">Read More</a></article>
    </div>
    <a class="view-all">View All Products</a>
  </div>
</section>

<section class="sustain">
  <div class="backdrop" role="img" aria-label="Leafy recycling symbol standing on a grass field under blue sky"></div>
  <div class="wrap">
    <h2>SUSTAINABILITY</h2>
    <p>Lorem Ipsum is simply dummy text of the printing and typesetting industry. Lorem Ipsum has been the industry's standard dummy text ever since the 1500s, when an unknown printer took a galley.</p>
    <a class="btn">Read More</a>
  </div>
</section>

<section class="blog">
  <div class="wrap">
    <h2 class="section-title">Latest Blog</h2>
    <span class="rule"></span>
    <div class="blog-grid">
      <article class="blog-card">
        <div class="blog-photo photo-rock" role="img" aria-label="Limestone pavement with a lone tree at sunset"></div>
        <h3>Lorem Ipsum is simply dummy text of the printing</h3>
        <p>There are many variations of passages of Lorem Ipsum avail able, but the majority have.</p>
        <a class="btn">Read More</a>
      </article>
      <article class="blog-card">
        <div class="blog-photo photo-valley" role="img" aria-label="Green valley with floating environmental icons"></div>
        <h3>Lorem Ipsum is simply dummy text of the printing</h3>
        <p>There are many variations of passages of Lorem Ipsum avail able, but the majority have.</p>
        <a class="btn">Read More</a>
      </article>
      <article class="blog-card">
        <div class="blog-photo photo-bulb" role="img" aria-label="Glowing light bulb with a tree inside held over an open hand"></div>
        <h3>Lorem Ipsum is simply dummy text of the printing</h3>
        <p>There are many variations of passages of Lorem Ipsum avail able, but the majority have.</p>
        <a class="btn">Read More</a>
      </article>
    </div>
  </div>
</section>

<section class="cta">
  <div class="backdrop" role="img" aria-label="Rocky limestone landscape at dusk"></div>
  <div class="cta-body">
    <h2>LOREM IPSUM IS SIMPLY DUMMY TEXT OF THE PRINTING</h2>
    <p>Sed ut perspiciatis unde omnis iste natus error sit voluptatem accusantium dolore mque laudantium, totam rem aperiam, eaque ipsa quae ab illo inventore</p>
    <a class="btn">Contact Us</a>
  </div>
</section>

<footer class="site-footer">
  <div class="wrap footer-top">
    <div class="footer-brand">Kestal Materials</div>
    <div class="footer-col col-menu">
      <h4>MENU</h4>
      <ul><li>HOME</li><li>ABOUT US</li><li>PRODUCTS</li><li>LOCATIONS</li><li>SUSTAINABILITY</li><li>CAREERS</li><li>CONTACT US</li></ul>
    </div>
    <div class="footer-col col-contact">
      <h4>CONTACT US</h4>
      <div class="info"><span class="ico"><svg width="10" height="13" viewBox="0 0 10 13"><path d="M5 0a5 5 0 0 0-5 5c0 3.5 5 8 5 8s5-4.5 5-8a5 5 0 0 0-5-5zm0 7a2 2 0 1 1 0-4 2 2 0 0 1 0 4z" fill="#1d1d1d"/></svg></span><span>2207 Ridgeline Road<br>Calder, AB T0H 4K0</span></div>
      <div class="info"><span class="ico"><svg width="12" height="12" viewBox="0 0 12 12"><path d="M2.4 0.6l2 2.2-1 1.4a7 7 0 0 0 4.4 4.4l1.4-1 2.2 2-1.2 1.8C5.6 11.2.8 6.4.6 1.8z" fill="#1d1d1d"/></svg></span><span>Call Us<br>555.014.2290</span></div>
      <div class="info"><span class="ico"><svg width="12" height="9" viewBox="0 0 12 9"><path d="M0 0h12v9H0z" fill="#1d1d1d"/><path d="M0 0l6 5 6-5" stroke="#fff" fill="none"/></svg></span><span>E mail Us<br>info@KestalMaterials.com</span></div>
    </div>
    <div class="footer-col col-follow">
      <h4>FOLLOW US</h4>
      <div class="info"><span class="ico"></span><span>Like us on<br>FRIENDLINE</span></div>
      <div class="info"><span class="ico"></span><span>Follow us on<br>CHIRPNET</span></div>
      <div class="info"><span class="ico"></span><span>Follow us on<br>WORKLINK</span></div>
    </div>
  </div>
  <div class="footer-line"></div>
  <p class="copyright">Copyright © 2021 All Rights Reserved</p>
</footer>

</body>
</html>
```